Business card design for Brivo Engineering Tandem

We need a new business card design along with all the necessary to place an order. The company is Brivo Engineering Tandem and we recently updated our logo.

```html
<!DOCTYPE html>
<html lang="en">
<head>
<meta charset="utf-8">
<title>Brivo Engineering Tandem – Business Card</title>
<link rel="stylesheet" href="https://fonts.googleapis.com/css2?family=Poppins:wght@400;500&family=Raleway:wght@700&display=swap">
<style>
  :root {
    --backdrop: #d8d8d8;
    --card-white: #ffffff;
    --card-grey: #959595;
    --accent: #e1bb22;
    --ink: #8a8a8a;
    --ink-dark: #5f5f5f;
  }
  * { margin: 0; padding: 0; box-sizing: border-box; }
  html, body {
    width: 1093px;
    height: 1200px;
    overflow: hidden;
    background: var(--backdrop);
  }
  .stage {
    position: relative;
    width: 1093px;
    height: 1200px;
  }
  .card {
    position: absolute;
    left: 264px;
    height: 357px;
    box-shadow: 0 6px 18px rgba(0,0,0,0.18);
    overflow: hidden;
  }
  .card::after {
    content: "";
    position: absolute;
    left: 0; right: 0; bottom: 0;
    height: 6px;
    background: var(--accent);
  }
  .card--front { top: 226px; width: 578px; background: var(--card-white); }
  .card--back  { top: 620px; width: 582px; background: var(--card-grey); }

  .holder {
    position: absolute;
    left: 26px;
    top: 38px;
  }
  .holder__name {
    font-family: "Raleway", sans-serif;
    font-weight: 700;
    font-size: 23px;
    line-height: 1.05;
    color: var(--ink);
    letter-spacing: 0.2px;
  }
  .holder__role {
    font-family: "Poppins", sans-serif;
    font-weight: 400;
    font-size: 17px;
    line-height: 1.2;
    color: var(--accent);
  }

  .brand {
    position: absolute;
    display: flex;
    align-items: center;
    gap: 9px;
    font-family: "Poppins", sans-serif;
    font-weight: 500;
    white-space: nowrap;
  }
  .brand__mark {
    flex: none;
    background: var(--accent);
  }
  .brand--front {
    right: 27px;
    top: 50px;
    font-size: 17px;
    color: var(--ink);
  }
  .brand--front .brand__mark { width: 14px; height: 14px; }
  .brand--back {
    left: 0; right: 0;
    top: 160px;
    justify-content: center;
    font-size: 30px;
    color: var(--ink-dark);
  }
  .brand--back .brand__mark { width: 26px; height: 26px; }

  .contacts {
    position: absolute;
    left: 26px;
    top: 265px;
    list-style: none;
    font-family: "Poppins", sans-serif;
    font-size: 17px;
    line-height: 21px;
    color: var(--ink);
  }
  .contacts__item {
    display: flex;
    align-items: center;
    gap: 7px;
  }
  .contacts__icon {
    width: 15px;
    height: 15px;
    flex: none;
    fill: none;
    stroke: var(--accent);
    stroke-width: 1.6;
  }
  .address {
    position: absolute;
    right: 26px;
    top: 286px;
    text-align: right;
    font-style: normal;
    font-family: "Poppins", sans-serif;
    font-size: 17px;
    line-height: 21px;
    color: var(--ink);
  }
</style>
</head>
<body>
<main class="stage">
  <section class="card card--front" aria-label="Business card front">
    <header class="holder">
      <h1 class="holder__name">DORIAN PELLWICK</h1>
      <p class="holder__role">Managing Director</p>
    </header>

    <div class="brand brand--front">
      <span class="brand__mark"></span>
      <span class="brand__name">Brivo Engineering Tandem</span>
    </div>

    <ul class="contacts">
      <li class="contacts__item">
        <svg class="contacts__icon" viewBox="0 0 16 16" aria-hidden="true">
          <path d="M3 2l3 0 1 3.5-2 1.2a8 8 0 0 0 4.3 4.3l1.2-2 3.5 1v3a1.5 1.5 0 0 1-1.5 1.5A12 12 0 0 1 1.5 3.5 1.5 1.5 0 0 1 3 2z"/>
        </svg>
        <span>061-482 731 905</span>
      </li>
      <li class="contacts__item">
        <svg class="contacts__icon" viewBox="0 0 16 16" aria-hidden="true">
          <rect x="1" y="3.5" width="14" height="9" fill="#e1bb22" stroke="none"/>
          <path d="M1 3.5l7 5.5 7-5.5" stroke="#ffffff" stroke-width="1.2"/>
        </svg>
        <span>hello@brivotandem.com</span>
      </li>
      <li class="contacts__item">
        <svg class="contacts__icon" viewBox="0 0 16 16" aria-hidden="true">
          <circle cx="8" cy="8" r="6.5"/>
          <ellipse cx="8" cy="8" rx="3" ry="6.5"/>
          <path d="M1.5 8h13M2.5 4.8h11M2.5 11.2h11"/>
        </svg>
        <span>www.brivotandem.com</span>
      </li>
    </ul>

    <address class="address">
      87, Kestrel Works Road<br>
      30718,Norland
    </address>
  </section>

  <section class="card card--back" aria-label="Business card back">
    <div class="brand brand--back">
      <span class="brand__mark"></span>
      <span class="brand__name">Brivo Engineering Tandem</span>
    </div>
  </section>
</main>
</body>
</html>
```